High profile consulting company needs a Business Card Design

I need a business card design for a coaching /consulting company. We specialize in changing behaviors. Our services include therapy, workshops, life coaching, etc.

Check out our website to get a feel for our personality. www.oakbridgeadvisory.com

The new logo will be attached to the website soon, I have attached the new logo for your use on the business card.
Updates

I forgot to provide you with the company email under the "must have" section for the business card.  The website is:

 www.oakbridgeadvisory.com

I understand there's some trouble with the logo I uploaded.  I will try that again.  Thank you for your efforts.

Dana

Thank you for some of your questions.  I prefer a one sided business card, and tend to like the white backgrounds.

I also made 2 small changes to the content.  

add MFT after the name:  Dana Holloway, MFT

and the tag line needed more clarity once I saw it.  Please change it to:  Improving performance by strengthening relationships and changing behaviors.

Thank you,
Dana

Industry/Entity Type

Business

Requirements
Must have
• logo
Phone number: 415-207-5146
email: Dana@oakbridgeadvisory.com
Dana Holloway, MFT
President
Nice to have
• Improving performance by strengthening relationships and changing behaviors.

```html
<!DOCTYPE html>
<html lang="en">
<head>
<meta charset="utf-8">
<title>Oakbridge Advisory – Business Card</title>
<link rel="stylesheet" href="https://fonts.googleapis.com/css2?family=Jost:wght@400;500;600&display=swap">
<style>
  :root {
    --brand-green: #046a50;
    --card-white: #f7f7f7;
    --ink-dark: #2e2e2e;
    --ink-grey: #6b6b6b;
    --mark-grey: #8a8a8a;
    --backdrop: #e4e4e2;
  }
  * { box-sizing: border-box; margin: 0; padding: 0; }
  html, body { width: 1200px; height: 900px; overflow: hidden; }
  body {
    background: var(--backdrop);
    font-family: "Jost", "Futura", sans-serif;
    position: relative;
  }
  .card {
    position: absolute;
    left: 320px;
    width: 560px;
    height: 320px;
    border-radius: 26px;
    overflow: hidden;
    box-shadow: 0 6px 18px rgba(0,0,0,0.14);
  }
  .card-front {
    top: 90px;
    background: var(--brand-green);
    display: flex;
    flex-direction: column;
    align-items: center;
    justify-content: center;
    gap: 14px;
  }
  .front-mark {
    width: 64px; height: 64px;
    border: 4px solid #fff;
    border-radius: 50%;
  }
  .front-name {
    color: #fff;
    font-weight: 600;
    font-size: 30px;
    letter-spacing: 1px;
    text-align: center;
    line-height: 1.15;
  }
  .card-back {
    top: 490px;
    background: var(--card-white);
  }
  .back-arc { position: absolute; inset: 0; }
  .back-mark {
    position: absolute;
    left: 62px; top: 105px;
    width: 110px; height: 110px;
    border: 6px solid var(--mark-grey);
    border-radius: 50%;
    display: flex;
    align-items: center;
    justify-content: center;
    text-align: center;
    color: var(--mark-grey);
    font-weight: 600;
    font-size: 13px;
    line-height: 1.2;
  }
  .holder {
    position: absolute;
    left: 272px; top: 82px;
  }
  .holder-name {
    color: var(--ink-dark);
    font-weight: 600;
    font-size: 21px;
  }
  .holder-title {
    color: var(--ink-grey);
    font-size: 16px;
    margin-top: 2px;
  }
  .contact-list {
    list-style: none;
    position: absolute;
    left: 272px; top: 172px;
    color: var(--ink-grey);
    font-size: 15px;
  }
  .contact-list li {
    display: flex;
    align-items: center;
    gap: 8px;
    line-height: 23px;
  }
  .contact-icon { width: 13px; height: 13px; flex: none; }
</style>
</head>
<body>

  <section class="card card-front" aria-label="Card front">
    <div class="front-mark"></div>
    <div class="front-name">OAKBRIDGE ADVISORY</div>
  </section>

  <section class="card card-back" aria-label="Card back">
    <svg class="back-arc" viewBox="0 0 560 320" aria-hidden="true">
      <circle cx="-130" cy="160" r="330" fill="none" stroke="var(--brand-green)" stroke-width="14"/>
    </svg>
    <div class="back-mark">OAKBRIDGE<br>ADVISORY</div>

    <div class="holder">
      <div class="holder-name">Dana Holloway, MFT</div>
      <div class="holder-title">President</div>
    </div>

    <ul class="contact-list">
      <li>
        <svg class="contact-icon" viewBox="0 0 16 16" aria-hidden="true"><path fill="var(--brand-green)" d="M1 5c0-2 3-3 7-3s7 1 7 3v1h-4V5H5v1H1zM3 8h10l1 6H2z"/></svg>
        415-207-5146 www.oakbridgeadvisory.com
      </li>
      <li>
        <svg class="contact-icon" viewBox="0 0 16 16" aria-hidden="true"><rect x="1" y="3" width="14" height="10" fill="none" stroke="var(--brand-green)" stroke-width="1.8"/><path d="M1 3l7 6 7-6" fill="none" stroke="var(--brand-green)" stroke-width="1.8"/></svg>
        Dana@oakbridgeadvisory.com
      </li>
      <li>
        <svg class="contact-icon" viewBox="0 0 16 16" aria-hidden="true"><circle cx="8" cy="8" r="6.5" fill="none" stroke="var(--brand-green)" stroke-width="1.6"/><path d="M1.5 8h13M8 1.5c-3 3-3 10 0 13M8 1.5c3 3 3 10 0 13" fill="none" stroke="var(--brand-green)" stroke-width="1.3"/></svg>
        www.oakbridgeadvisory.com
      </li>
    </ul>
  </section>

</body>
</html>
```